Varentoria Business Card and Letter Head

We are a leadership assessment consultancy based in Sydney, Australia. We help executive-level decison-makers select leaders for more senior level roles in corporate and government organisations. Our methodology is based on the latest research from the field of neuroscience.
We need a business card design and matching letter head that presents our company, Varentoria, as a:
1. trusted adviser to senior executive-level decison makers
2. niche consultancy who are experts in the field of assessing leadership talent
3. results-focused solution provider who balance scientific methods with pragmatic solutions
The following company details should be used in all designs:
Company Name: Varentoria
Details (for business card):
Derek Hanford
Prime Capacity Officer
Level 29, Marlow Tower
7 Marlow Square
Sydney, NSW 2000 Australia
Phone: 1300 582 714
Mobile: 0412 637 258
Email: derek.hanford@varentoria-example.com.au
Website: varentoria-example.com.au
I have attached the logo for Varentoria (for both a white and black background) - your business card and letter head designs must incoporate this logo and colour scheme.
Thanks for your interest in this project, I'm looking forward to receiving your ideas.
Regards,
Derek
Target Market(s)
Executive-level decison-makers in corporate and government organisations (e.g., CEO, VP, Head of Human Resources)
Industry/Entity Type
Leadership
Look and feel

```html
<!DOCTYPE html>
<html lang="en">
<head>
<meta charset="utf-8">
<title>Varentoria Business Card</title>
<link rel="stylesheet" href="https://fonts.googleapis.com/css2?family=Open+Sans:wght@400;600;700&display=swap">
<style>
  :root {
    --stage: #ece9e4;
    --card-white: #ffffff;
    --charcoal: #414143;
    --brand-red: #c0301f;
    --text-light: #f2f2f2;
    --text-dark: #3b3b3d;
  }
  * { margin: 0; padding: 0; box-sizing: border-box; }
  html, body {
    width: 1200px; height: 469px; overflow: hidden;
    background: var(--stage);
    font-family: "Open Sans", Arial, sans-serif;
  }
  .canvas { position: relative; width: 1200px; height: 469px; }
  .card {
    position: absolute; top: 83px; width: 525px; height: 300px;
    border-radius: 26px; overflow: hidden;
  }
  .card--front { left: 45px; background: var(--card-white); }
  .card--back { left: 622px; background: var(--brand-red); }
  .card__wave { position: absolute; inset: 0; }

  .brand { position: absolute; display: flex; align-items: center; gap: 12px; }
  .brand__square { width: 34px; height: 34px; }
  .brand__name { font-weight: 700; font-size: 36px; letter-spacing: -0.5px; line-height: 1; }
  .card--front .brand { left: 128px; top: 75px; }
  .card--front .brand__square { background: var(--text-dark); }
  .card--front .brand__name { color: var(--text-dark); }
  .card--back .brand { left: 128px; top: 108px; }
  .card--back .brand__square { background: var(--card-white); }
  .card--back .brand__name { color: var(--card-white); }

  .back-web {
    position: absolute; left: 0; right: 0; top: 201px;
    text-align: center; color: var(--card-white);
    font-size: 13px; letter-spacing: 1px;
  }

  .holder { position: absolute; left: 25px; top: 239px; color: var(--text-light); text-align: left; }
  .holder__name { font-weight: 700; font-size: 14px; line-height: 17px; }
  .holder__title { font-size: 11.5px; line-height: 14px; }
  .divider { position: absolute; left: 147px; top: 216px; width: 1px; height: 54px; background: var(--text-light); opacity: .8; }

  .contact { position: absolute; left: 157px; color: var(--text-light); font-size: 11px; line-height: 14px; white-space: nowrap; }
  .contact--address { top: 218px; }
  .contact-row { display: flex; align-items: center; gap: 5px; position: absolute; color: var(--text-light); font-size: 11px; white-space: nowrap; }
  .contact-row svg { width: 10px; height: 10px; fill: var(--text-light); }
  .row-phone { left: 157px; top: 240px; }
  .row-mobile { left: 157px; top: 256px; }
  .row-email { left: 258px; top: 240px; }
  .row-web { left: 258px; top: 256px; }
</style>
</head>
<body>
<main class="canvas">
  <section class="card card--front" aria-label="Business card front">
    <svg class="card__wave" viewBox="0 0 525 300" aria-hidden="true">
      <path d="M0,128 Q262,232 525,136 L525,144 Q262,240 0,138 Z" fill="var(--brand-red)"/>
      <path d="M0,144 Q262,244 525,150 L525,300 L0,300 Z" fill="var(--charcoal)"/>
    </svg>
    <div class="brand">
      <span class="brand__square"></span>
      <span class="brand__name">Varentoria</span>
    </div>
    <div class="holder">
      <p class="holder__name">Derek Hanford</p>
      <p class="holder__title">Prime Capacity Officer</p>
    </div>
    <span class="divider"></span>
    <p class="contact contact--address">Level 29, Marlow Tower 7 Marlow Square Sydney, NSW 2000 Australia</p>
    <p class="contact-row row-phone">
      <svg viewBox="0 0 10 10"><path d="M2,0.5 L4,2.8 L3,4 Q4.5,6 6,7 L7.2,6 L9.5,8 L8,9.6 Q3,9 0.4,2 Z"/></svg>1300 582 714
    </p>
    <p class="contact-row row-mobile">
      <svg viewBox="0 0 10 10"><rect x="2.5" y="0" width="5" height="10" rx="1"/></svg>0412 637 258
    </p>
    <p class="contact-row row-email">
      <svg viewBox="0 0 10 10"><path d="M0,2 L10,2 L10,8 L0,8 Z M0.5,2.5 L5,5.5 L9.5,2.5" /></svg>derek.hanford@varentoria-example.com.au
    </p>
    <p class="contact-row row-web">
      <svg viewBox="0 0 10 10"><circle cx="5" cy="5" r="4.6"/></svg>www.varentoria-example.com.au
    </p>
  </section>

  <section class="card card--back" aria-label="Business card back">
    <div class="brand">
      <span class="brand__square"></span>
      <span class="brand__name">Varentoria</span>
    </div>
    <p class="back-web">www.varentoria-example.com.au</p>
  </section>
</main>
</body>
</html>
```